Professional Engineering Web Design

Project Brief: Website Redesign for Mechanical Design Consultancy
Project Overview
I want to update and improve my current website to create a more professional, modern, and high-credibility online presence for my mechanical design consultancy.

Current site: https://valtorix.design/

The new website must communicate expertise, precision, and trust—matching the standard of top engineering and product design agencies.

Reference Websites (Style + Structure Inspiration)
These represent the quality, cleanliness, and professionalism I want to achieve:

https://plinthwaredesign.com/
https://www.sorvane.com/
https://bramlow-uk.com/
Brand Look
Professional, modern, engineering-focused aesthetic
Clean layouts and strong typography
High-quality imagery conveying precision, innovation, and mechanical expertise
Colour scheme and styling must follow my existing logo (attached in project)
Platform Requirements
The website must be built on WordPress
Should use a clean, flexible theme or modern page builder (Elementor, Gutenberg, Bricks, or similar)
Avoid overly complex custom coding so I can easily edit content later
Final deliverable must allow me to manage and update content without developer assistance
Functionality
Fast-loading, lightweight, and smooth user experience
Clean animations and transitions similar to the reference sites
Fully mobile responsive
Clear navigation and strong visual hierarchy
Contact forms optimised for lead generation
Optional: subtle scroll effects, case study sliders, icon animations, etc.
SEO Aspirations
Developer should recommend and implement a modern SEO strategy
Proper on-page SEO setup (titles, meta, schema, alt tags, heading structure)
Optimised site architecture for ranking and crawling
Aim: Generate leads through improved visibility and keyword targeting
Optional but useful: Google Analytics, Google Search Console setup
User Journeys
(Recommended structure)

The site should be crafted around clear, intuitive journeys for each type of visitor:

Potential new clients
Quickly understand what services I offer
View examples of past work / case studies
See credibility indicators (process, expertise, industries served)
Easily contact me or request a project discussion
Returning clients
Access updated portfolio items
Find contact details or book follow-up work easily
General visitors discovering through SEO
Be guided to core service areas
Understand my value proposition quickly
Be invited to learn more or make contact
The developer should design the structure to support these journeys smoothly.

Maintenance Expectations
Website will be maintained by me, so it should be easy to update using relatively basic WordPress skills
Use modular templates and simple backend structure
Avoid unnecessary plugins
Provide brief handover documentation if required
Hosting Preferences
Site is currently hosted via a family member
Open to discussing moving to a paid, reliable hosting provider if preferable for performance and maintainability
Developer may advise on the best hosting setup for WordPress
Content
Most content can be taken from the existing website
Developer is welcome to suggest improvements to structure, layout, and imagery
Must remain easy for me to edit or add new content later (e.g., new projects)
Deliverables
Fully built WordPress website
Clean, professional, modern design inspired by the reference sites
Mobile-responsive across all devices
SEO-ready structure and optimisations
Transfer of website and admin rights
Any design assets, templates, or documentation used

```html
<!DOCTYPE html>
<html lang="en">
<head>
<meta charset="utf-8">
<title>Valtorix Mechanical Design — Mechanical CAD Design</title>
<link rel="stylesheet" href="https://fonts.googleapis.com/css2?family=Urbanist:wght@400;500;600;700;800&display=swap">
<style>
:root{
  --blue:#2b5cf3;
  --blue-dark:#1c3fb8;
  --navy:#18306e;
  --ink:#1f2230;
  --text:#4a4d5a;
  --muted:#6c7080;
  --lavender:#e8ecfb;
  --white:#ffffff;
  --star:#f5a524;
  --line:#d8dcea;
}
*{box-sizing:border-box;margin:0;padding:0}
html,body{width:1200px;height:4584px;overflow:hidden}
body{font-family:"Urbanist",sans-serif;color:var(--ink);background:var(--white);position:relative}
.abs{position:absolute}
a{color:inherit;text-decoration:none}
.btn{position:absolute;display:flex;align-items:center;justify-content:center;background:var(--blue);color:var(--white);border-radius:30px;font-weight:600;font-size:12px;letter-spacing:.3px;box-shadow:0 0 0 3px var(--white),0 0 0 4px var(--blue)}
.btn.plain{box-shadow:none}
.eyebrow{position:absolute;color:var(--blue);font-size:14px;font-weight:500}
.heading{position:absolute;font-size:32px;font-weight:600;color:var(--ink);line-height:1}
.heading span{color:var(--blue)}
.rule{position:absolute;height:3px;width:44px;background:var(--blue);border-radius:2px}
.center{left:0;width:1200px;text-align:center}
.rule.center-rule{left:578px}

/* top bar */
.topbar{top:0;left:0;width:1200px;height:36px;background:#f3f4f7}
.social-dot{position:absolute;top:11px;width:13px;height:13px;border-radius:3px;background:var(--blue)}
.contact-chip{position:absolute;top:6px;display:flex;align-items:center;gap:10px;font-size:12px;color:var(--ink)}
.contact-chip .ic{width:24px;height:24px;border-radius:50%;background:var(--blue);display:flex;align-items:center;justify-content:center}

/* header */
.header{top:36px;left:0;width:1200px;height:80px;background:var(--white)}
.brand{position:absolute;display:flex;align-items:center;gap:10px}
.brand .mark{border-radius:50%;background:var(--blue)}
.brand .word{color:var(--blue);font-weight:700;line-height:1}
.nav{position:absolute;top:31px;font-size:12.5px;font-weight:600;color:var(--ink)}

/* hero */
.hero{top:116px;left:0;width:1200px;height:559px;
  background:
    radial-gradient(ellipse 380px 300px at 980px 180px,rgba(150,200,245,.55),rgba(150,200,245,0) 70%),
    radial-gradient(ellipse 300px 220px at 760px 330px,rgba(110,160,225,.45),rgba(110,160,225,0) 70%),
    radial-gradient(ellipse 420px 360px at 120px 480px,rgba(14,28,70,.7),rgba(14,28,70,0) 70%),
    linear-gradient(100deg,#16296a 0%,#1f3f8a 30%,#2e62b3 58%,#4a8ad0 80%,#78aee2 100%)}
.hero h1{position:absolute;left:140px;top:146px;color:var(--white);font-weight:800;line-height:1}
.hero .l1{font-size:54px;display:block}
.hero .l2{font-size:68px;display:block;margin-top:14px}
.hero .sub{position:absolute;left:140px;top:300px;color:var(--white);font-size:32px;font-weight:500}
.scroll-btn{position:absolute;left:562px;top:638px;width:72px;height:72px;border-radius:50%;background:var(--white);box-shadow:0 4px 14px rgba(0,0,0,.12);display:flex;align-items:center;justify-content:center}

/* welcome */
.para{position:absolute;font-size:11.6px;line-height:23px;color:var(--text)}
.photo-ring{position:absolute;border-radius:50%;border:10px solid #454545;box-shadow:0 0 0 2px #d9d9d9}
.ground{position:absolute;border-radius:50%;background:radial-gradient(ellipse at center,rgba(0,0,0,.18),rgba(0,0,0,0) 70%)}
.logo-disc{position:absolute;border-radius:50%;background:var(--blue);border:6px solid var(--white)}

/* band */
.band{top:1289px;left:0;width:1200px;height:148px;background:var(--blue);color:var(--white);text-align:center}
.band h2{position:absolute;top:29px;width:100%;font-size:23px;font-weight:600}
.band p{position:absolute;top:63px;width:100%;font-size:13.5px;line-height:23px;font-weight:500}

/* expertise */
.card-img{position:absolute;top:1627px;width:283px;height:247px;border-radius:4px}
.card-icon{position:absolute;top:1753px;width:64px;height:64px;background:var(--blue);border-radius:4px;display:flex;align-items:center;justify-content:center}
.card-body{position:absolute;top:1825px;width:235px;height:140px;background:var(--white);padding:18px 0 0 22px}
.card-body h3{font-size:17px;font-weight:600;line-height:27px;color:var(--ink)}
.card-body p{margin-top:10px;font-size:11.5px;line-height:23px;color:var(--text)}
.decor{position:absolute;background:radial-gradient(ellipse at center,rgba(150,168,230,.28),rgba(150,168,230,0) 72%)}

/* projects */
.projects{top:2092px;left:0;width:1200px;height:829px;background:var(--lavender)}
.tile{position:absolute;border-radius:10px;border:4px solid #e2e3ea;box-shadow:0 2px 8px rgba(40,50,90,.08)}
.feature{position:absolute;left:141px;top:2316px;width:283px;height:431px;border-radius:10px;background:#dfe2ea;padding:10px}
.feature .inner{width:100%;height:100%;border-radius:6px;color:var(--white);text-align:center;position:relative;
  background:
    radial-gradient(ellipse 110px 150px at 130px 200px,rgba(20,40,140,.45),rgba(20,40,140,0) 75%),
    linear-gradient(180deg,#3d68ec 0%,#2f5be6 50%,#2a52d8 100%)}

/* about */
.sub-note{position:absolute;font-size:12px;color:var(--text)}

/* reviews */
.reviews{top:3537px;left:0;width:1200px;height:571px;background:var(--lavender)}
.review{position:absolute;top:3770px;width:290px;height:173px;background:var(--white);border-radius:8px;padding:34px 24px 0 26px;font-size:11px;line-height:23px;color:var(--text)}
.review.active{background:var(--blue);color:var(--white)}
.tail{position:absolute;top:3942px;width:0;height:0;border-left:40px solid transparent;border-top:36px solid var(--white)}
.quote{position:absolute;top:3750px}
.who{position:absolute;top:3962px;font-size:14px;font-weight:600;color:var(--ink)}
.who small{display:block;font-size:11px;font-weight:500;color:var(--muted);line-height:14px}
.stars{position:absolute;top:4003px;color:var(--star);font-size:17px;letter-spacing:2px}
.arrow{position:absolute;top:3842px;width:32px;height:32px;border:1.5px solid var(--blue);border-radius:5px;display:flex;align-items:center;justify-content:center;background:var(--white)}

/* cta */
.cta{top:4108px;left:0;width:1200px;height:124px;background:var(--blue)}
.cta h2{position:absolute;left:206px;top:34px;font-size:46px;font-weight:600;color:var(--white)}
.cta .see{position:absolute;left:789px;top:41px;width:140px;height:42px;border-radius:30px;background:var(--blue-dark);color:var(--white);font-size:15px;font-weight:600;display:flex;align-items:center;justify-content:center;box-shadow:0 0 0 3px var(--white)}

/* footer */
.foot-title{position:absolute;top:4328px;font-size:16px;font-weight:600;color:var(--ink)}
.foot-title span{color:var(--blue)}
.foot-rule{position:absolute;top:4356px;width:44px;height:2px;background:var(--blue)}
.foot-link{position:absolute;left:366px;font-size:11.5px;color:var(--text)}
.foot-contact{position:absolute;left:594px;font-size:11px;line-height:15px;color:var(--text)}
.foot-ic{position:absolute;left:560px;width:24px;height:24px;border-radius:50%;border:1.5px solid var(--blue);display:flex;align-items:center;justify-content:center}
.foot-social{position:absolute;top:4455px;width:26px;height:26px;border-radius:50%;border:1.5px solid var(--blue)}
.copyright{position:absolute;top:4546px;left:0;width:1200px;text-align:center;font-size:11.5px;color:var(--text)}
</style>
</head>
<body>

<!-- Top bar -->
<div class="abs topbar">
  <span class="social-dot" style="left:582px"></span>
  <span class="social-dot" style="left:606px"></span>
  <span class="social-dot" style="left:630px"></span>
  <span class="social-dot" style="left:654px"></span>
  <div class="contact-chip" style="left:706px">
    <span class="ic"><svg width="12" height="10" viewBox="0 0 12 10"><rect x="0.5" y="0.5" width="11" height="9" rx="1" fill="none" stroke="#fff"/><path d="M1 1l5 4 5-4" fill="none" stroke="#fff"/></svg></span>
    info@valtorix.design
  </div>
  <div class="contact-chip" style="left:906px">
    <span class="ic"><svg width="12" height="12" viewBox="0 0 24 24"><path d="M6.6 10.8a15 15 0 006.6 6.6l2.2-2.2a1 1 0 011-.25 11.4 11.4 0 003.6.6 1 1 0 011 1V20a1 1 0 01-1 1A17 17 0 013 4a1 1 0 011-1h3.5a1 1 0 011 1c0 1.25.2 2.45.6 3.6a1 1 0 01-.25 1z" fill="#fff"/></svg></span>
    +44 (0) 7700 900482
  </div>
</div>

<!-- Header -->
<header class="abs header">
  <div class="brand" style="left:140px;top:8px">
    <span class="mark" style="width:64px;height:64px"></span>
    <span>
      <span class="word" style="font-size:40px;display:block;letter-spacing:3px">valtorix</span>
      <span class="word" style="font-size:11px;display:block;letter-spacing:1.5px;margin-top:4px;font-weight:600">MECHANICAL DESIGN</span>
    </span>
  </div>
  <a class="nav" style="left:477px">HOME</a>
  <a class="nav" style="left:563px">ABOUT US</a>
  <a class="nav" style="left:674px">OUR SERVICES</a>
  <a class="nav" style="left:810px">PORTFOLIO</a>
  <a class="btn plain" style="left:929px;top:17px;width:128px;height:42px;font-size:12px">CONTACT US</a>
</header>

<!-- Hero -->
<section class="abs hero" role="img" aria-label="Blue technical drawing background of mechanical parts and gears">
  <h1><span class="l1">Mechanical</span><span class="l2">CAD Design</span></h1>
  <p class="sub">Cutting Edge Engineering</p>
  <a class="btn plain" style="left:140px;top:373px;width:130px;height:41px">CONTACT US</a>
</section>
<div class="scroll-btn">
  <svg width="14" height="14" viewBox="0 0 14 14"><path d="M3 3l4 4 4-4M3 7l4 4 4-4" fill="none" stroke="#1f2230" stroke-width="1.6"/></svg>
</div>

<!-- Welcome -->
<div class="decor" role="img" aria-label="Faint line drawing of a machine assembly" style="left:-30px;top:1030px;width:300px;height:230px"></div>
<p class="eyebrow" style="left:142px;top:801px">Welcome To</p>
<h2 class="heading" style="left:142px;top:824px">Valtorix <span>Mechanical Design</span></h2>
<span class="rule" style="left:142px;top:867px"></span>
<div class="para" style="left:142px;top:883px;width:405px">
  <p>Welcome to Valtorix Mechanical Design. We are a UK based design consultancy offering a comprehensive mechanical and product design service from initial concepts through to full volume production.</p>
  <p style="margin-top:4px">At Valtorix Mechanical Design, we are committed to delivering innovative, high-quality engineering solutions tailored to meet the needs of our clients. Specializing in the design, development, and optimization of mechanical systems, we combine years of industry expertise with cutting-edge technology to ensure efficiency and precision in every project we undertake.</p>
</div>
<a class="btn" style="left:145px;top:1116px;width:135px;height:38px">Contact us Today</a>
<div class="ground" style="left:600px;top:1172px;width:420px;height:40px"></div>
<div class="photo-ring" role="img" aria-label="Engineers working on CAD models at computer screens" style="left:634px;top:768px;width:426px;height:426px;
  background:
    radial-gradient(ellipse 120px 160px at 300px 170px,rgba(235,215,195,.55),rgba(235,215,195,0) 70%),
    radial-gradient(ellipse 140px 90px at 150px 220px,rgba(40,160,170,.55),rgba(40,160,170,0) 75%),
    linear-gradient(180deg,#dfe6ee 0%,#b8c6d6 30%,#4c6278 62%,#20303f 100%)"></div>
<div class="logo-disc" style="left:576px;top:1016px;width:172px;height:172px"></div>

<!-- Band -->
<section class="abs band">
  <h2>Need reliable, accurate mechanical CAD designs for your project?</h2>
  <p>Whether you're developing prototypes, manufacturing parts, or optimizing existing systems,<br>our expert designers are ready to bring your concepts to life with cutting-edge CAD tools.</p>
</section>
<svg class="abs" style="left:560px;top:1436px" width="80" height="22" viewBox="0 0 80 22"><path d="M0 0 Q40 40 80 0Z" fill="#2b5cf3"/></svg>
<svg class="abs" style="left:592px;top:1425px" width="16" height="14" viewBox="0 0 14 14"><path d="M3 2l4 4 4-4M3 6l4 4 4-4" fill="none" stroke="#fff" stroke-width="1.6"/></svg>

<!-- Expertise -->
<p class="eyebrow center" style="top:1535px">Solutions</p>
<h2 class="heading center" style="top:1556px">Our <span>Expertise</span></h2>
<span class="rule center-rule" style="top:1598px"></span>

<div class="decor" role="img" aria-label="Faint line drawing of a machine assembly" style="left:930px;top:1800px;width:290px;height:290px"></div>

<div class="card-img" role="img" aria-label="Engineer in hard hat reviewing a product design on screen" style="left:141px;
  background:
    radial-gradient(ellipse 70px 90px at 210px 110px,rgba(240,225,210,.8),rgba(240,225,210,0) 70%),
    radial-gradient(ellipse 80px 90px at 70px 160px,rgba(120,150,110,.45),rgba(120,150,110,0) 75%),
    linear-gradient(180deg,#b9c4cf 0%,#8795a8 45%,#3f4a5a 100%)"></div>
<div class="card-icon" style="left:359px"><svg width="34" height="30" viewBox="0 0 34 30" fill="none" stroke="#fff" stroke-width="1.5"><circle cx="10" cy="12" r="7"/><circle cx="25" cy="10" r="5"/><circle cx="25" cy="10" r="2"/><path d="M4 28h14M10 19v9"/></svg></div>
<div class="card-body" style="left:189px"><h3>Bespoke<br>Product Design</h3><p>Innovative design from concept through the full development life cycle</p></div>

<div class="card-img" role="img" aria-label="Designer creating a 3D model on a computer" style="left:458px;
  background:
    radial-gradient(ellipse 90px 80px at 200px 70px,rgba(200,200,205,.75),rgba(200,200,205,0) 70%),
    radial-gradient(ellipse 60px 90px at 90px 110px,rgba(210,175,150,.55),rgba(210,175,150,0) 75%),
    linear-gradient(180deg,#6f7c94 0%,#39465e 55%,#151b27 100%)"></div>
<div class="card-icon" style="left:676px"><svg width="34" height="30" viewBox="0 0 34 30" fill="none" stroke="#fff" stroke-width="1.5"><rect x="3" y="3" width="28" height="18" rx="1"/><path d="M12 27h10M17 21v6"/><path d="M17 7l6 3v6l-6 3-6-3v-6z"/></svg></div>
<div class="card-body" style="left:506px"><h3>3D Modelling<br>and Drawings</h3><p>We create 3D CAD, 2D engineering drawings and photorealistic renders</p></div>

<div class="card-img" role="img" aria-label="Designer holding a printed prototype part at her desk" style="left:776px;
  background:
    radial-gradient(ellipse 80px 100px at 200px 100px,rgba(245,225,205,.8),rgba(245,225,205,0) 70%),
    radial-gradient(ellipse 70px 50px at 70px 170px,rgba(60,60,65,.5),rgba(60,60,65,0) 75%),
    linear-gradient(180deg,#e4e1da 0%,#c9c3b9 50%,#8f887d 100%)"></div>
<div class="card-icon" style="left:994px"><svg width="34" height="30" viewBox="0 0 34 30" fill="none" stroke="#fff" stroke-width="1.5"><rect x="3" y="3" width="28" height="18" rx="1"/><path d="M12 27h10M17 21v6"/><circle cx="17" cy="12" r="5"/><circle cx="17" cy="12" r="1.5"/></svg></div>
<div class="card-body" style="left:824px"><h3>Design for<br>Manufacture</h3><p>Creating designs optimised for prototype and production manufacture</p></div>

<!-- Projects -->
<section class="abs projects"></section>
<p class="eyebrow center" style="top:2192px">Our Work</p>
<h2 class="heading center" style="top:2213px">Recent <span>Projects</span></h2>
<span class="rule center-rule" style="top:2255px"></span>
<p class="sub-note center" style="top:2274px">A small selection of our previous projects</p>

<div class="feature">
  <div class="inner" role="img" aria-label="Electrical switchgear cabinet render under blue overlay">
    <p style="position:absolute;top:126px;width:100%;font-size:18px;font-weight:600">Electrical Switchgear</p>
    <p style="position:absolute;top:162px;width:100%;font-size:13.5px;line-height:24px;font-weight:500">Modern engineering applied to<br>70 year old relics</p>
    <a class="btn" style="left:64px;top:235px;width:134px;height:36px;background:var(--white);color:var(--ink);box-shadow:0 0 0 2px #2f5be6,0 0 0 3px #fff">View All Projects</a>
  </div>
</div>
<div class="tile" role="img" aria-label="Render of a chrome alloy wheel" style="left:434px;top:2316px;width:269px;height:206px;
  background:
    radial-gradient(circle at 135px 100px,#2a2a2a 0,#2a2a2a 14px,#cfcfcf 16px,#f1f1f1 40px,#8c8c8c 62px,#e9e9e9 76px,#5a5a5a 86px,rgba(200,200,200,0) 92px),
    radial-gradient(ellipse 160px 40px at 140px 185px,rgba(0,0,0,.18),rgba(0,0,0,0) 70%),
    linear-gradient(180deg,#f5f5f5,#cfcfcf)"></div>
<div class="tile" role="img" aria-label="Render of an action camera on a linear rail mount" style="left:723px;top:2316px;width:335px;height:206px;
  background:
    radial-gradient(ellipse 40px 38px at 70px 55px,#1f1f1f,rgba(31,31,31,0) 80%),
    linear-gradient(160deg,rgba(0,0,0,0) 38%,rgba(40,40,40,.55) 46%,rgba(0,0,0,0) 54%),
    radial-gradient(ellipse 26px 40px at 295px 60px,rgba(210,165,40,.7),rgba(210,165,40,0) 80%),
    linear-gradient(180deg,#fbfbfb,#dcdcdc)"></div>
<div class="tile" role="img" aria-label="Render of a go-kart chassis with steering wheel and seat" style="left:434px;top:2540px;width:337px;height:207px;
  background:
    radial-gradient(ellipse 110px 40px at 170px 145px,rgba(30,30,30,.65),rgba(30,30,30,0) 75%),
    radial-gradient(ellipse 30px 40px at 110px 95px,rgba(235,230,205,.9),rgba(235,230,205,0) 80%),
    radial-gradient(ellipse 30px 24px at 175px 55px,rgba(40,40,40,.55),rgba(40,40,40,0) 80%),
    linear-gradient(180deg,#f4f4f4,#c9c9c9)"></div>
<div class="tile" role="img" aria-label="Render of a dark gearbox housing" style="left:789px;top:2540px;width:269px;height:207px;
  background:
    radial-gradient(ellipse 105px 70px at 135px 100px,#1c1c1e 0%,#2c2c30 55%,rgba(60,60,64,0) 100%),
    linear-gradient(180deg,#eeeeee,#b8b8b8)"></div>

<a class="btn" style="left:532px;top:2786px;width:135px;height:38px">View All Projects</a>

<!-- About -->
<div class="decor" role="img" aria-label="Faint line drawing of a machine assembly" style="left:-40px;top:3240px;width:260px;height:280px"></div>
<div class="ground" style="left:400px;top:3415px;width:260px;height:36px"></div>
<div class="photo-ring" role="img" aria-label="Portrait photo of the chief engineer" style="left:142px;top:3015px;width:420px;height:420px;
  background:
    radial-gradient(ellipse 110px 140px at 200px 180px,rgba(215,165,135,.75),rgba(215,165,135,0) 75%),
    radial-gradient(ellipse 150px 100px at 200px 380px,rgba(35,35,40,.85),rgba(35,35,40,0) 80%),
    linear-gradient(180deg,#f2f2f2 0%,#e1e1e1 45%,#9a9590 100%)"></div>
<div class="logo-disc" style="left:461px;top:3266px;width:162px;height:162px"></div>

<p class="eyebrow" style="left:662px;top:3070px">About Me</p>
<h2 class="heading" style="left:662px;top:3091px">Owen <span>Marsh</span></h2>
<p class="para" style="left:662px;top:3150px;width:405px;font-size:13.5px;line-height:28px">Owen Marsh is the Chief Engineer at Valtorix Mechanical Design. He has 11 years experience working as a mechanical design engineer in multiple industries including high performance automotive, consumer products, medical, industrial plus many more. He has worked in multiple roles across a wide range of products.</p>
<a class="btn" style="left:665px;top:3342px;width:172px;height:36px">Tell us about your ideas</a>

<!-- Reviews -->
<section class="abs reviews"></section>
<p class="eyebrow center" style="top:3637px">Our Reviews</p>
<h2 class="heading center" style="top:3658px">What Our <span>Clients Say</span></h2>
<span class="rule center-rule" style="top:3700px;background:var(--line)"></span>
<p class="sub-note center" style="top:3718px">A small selection of our previous projects</p>

<div class="arrow" style="left:96px"><svg width="10" height="14" viewBox="0 0 10 14"><path d="M8 1L2 7l6 6" fill="none" stroke="#2b5cf3" stroke-width="1.6"/></svg></div>
<div class="arrow" style="left:1068px"><svg width="10" height="14" viewBox="0 0 10 14"><path d="M2 1l6 6-6 6" fill="none" stroke="#2b5cf3" stroke-width="1.6"/></svg></div>

<div class="review" style="left:141px">Rhys went above and beyond in all aspects of the job. He identified issues with the design that I had not foreseen, rebuilt the design from scratch to ensure no aspect was overlooked, and...</div>
<span class="tail" style="left:181px"></span>
<svg class="quote" style="left:166px" width="44" height="34" viewBox="0 0 44 34"><path d="M2 34V18C2 8 7 2 17 0v6c-5 2-7 5-7 10h7v18zM25 34V18c0-10 5-16 15-18v6c-5 2-7 5-7 10h7v18z" fill="#2b5cf3"/></svg>
<p class="who" style="left:229px">RHYS<small>Manager</small></p>
<p class="stars" style="left:229px">★★★★★</p>

<div class="review active" style="left:456px">Owen was an excellent teammate on my project. He leveraged his considerable knowledge to make valuable recommendations and guide the design process effectively. He was flexible with...</div>
<span class="tail" style="left:496px;border-top-color:var(--blue)"></span>
<svg class="quote" style="left:481px" width="44" height="34" viewBox="0 0 44 34"><path d="M2 34V18C2 8 7 2 17 0v6c-5 2-7 5-7 10h7v18zM25 34V18c0-10 5-16 15-18v6c-5 2-7 5-7 10h7v18z" fill="#2b5cf3"/></svg>
<p class="who" style="left:543px">TAMSIN<small>Manager</small></p>
<p class="stars" style="left:543px">★★★★★</p>

<div class="review" style="left:769px">"Owen's description of his abilities was accurate. He is very capable and responsive. He worked very quickly and efficiently, cheerfully incorporating suggestions and revisions within a short...</div>
<span class="tail" style="left:809px"></span>
<svg class="quote" style="left:794px" width="44" height="34" viewBox="0 0 44 34"><path d="M2 34V18C2 8 7 2 17 0v6c-5 2-7 5-7 10h7v18zM25 34V18c0-10 5-16 15-18v6c-5 2-7 5-7 10h7v18z" fill="#2b5cf3"/></svg>
<p class="who" style="left:857px">CALLUM BRODIE<small>Client</small></p>
<p class="stars" style="left:857px">★★★★★</p>

<!-- CTA -->
<section class="abs cta">
  <h2>Curious what else we do?</h2>
  <a class="see">SEE HERE</a>
</section>

<!-- Footer -->
<footer>
  <div class="brand" style="left:141px;top:4325px;flex-direction:column;gap:6px;align-items:center;width:112px">
    <span class="mark" style="width:58px;height:58px"></span>
    <span class="word" style="font-size:30px;letter-spacing:2px">valtorix</span>
    <span class="word" style="font-size:9px;letter-spacing:1px;font-weight:600;margin-top:-4px">MECHANICAL DESIGN</span>
  </div>
  <span class="foot-social" style="left:145px"></span>
  <span class="foot-social" style="left:183px"></span>
  <span class="foot-social" style="left:221px"></span>

  <p class="foot-title" style="left:366px">Quick <span>Links</span></p>
  <span class="foot-rule" style="left:366px"></span>
  <a class="foot-link" style="top:4372px">Home</a>
  <a class="foot-link" style="top:4397px">About Us</a>
  <a class="foot-link" style="top:4423px">Portfolio</a>
  <a class="foot-link" style="top:4448px">Our Services</a>
  <a class="foot-link" style="top:4474px">Contact Us</a>

  <p class="foot-title" style="left:558px">Contact Details</p>
  <span class="foot-rule" style="left:558px"></span>
  <span class="foot-ic" style="top:4378px"><svg width="10" height="12" viewBox="0 0 10 12"><path d="M5 11s4-4 4-6.5a4 4 0 00-8 0C1 7 5 11 5 11z" fill="none" stroke="#2b5cf3" stroke-width="1.2"/><circle cx="5" cy="4.5" r="1.3" fill="#2b5cf3"/></svg></span>
  <p class="foot-contact" style="top:4373px">123, Building Name, Street<br>South Wales, UK.</p>
  <span class="foot-ic" style="top:4418px"><svg width="11" height="11" viewBox="0 0 24 24"><path d="M6.6 10.8a15 15 0 006.6 6.6l2.2-2.2a1 1 0 011-.25 11.4 11.4 0 003.6.6 1 1 0 011 1V20a1 1 0 01-1 1A17 17 0 013 4a1 1 0 011-1h3.5a1 1 0 011 1c0 1.25.2 2.45.6 3.6a1 1 0 01-.25 1z" fill="#2b5cf3"/></svg></span>
  <p class="foot-contact" style="top:4413px">Phone<br>+44 (0)7700 900 482</p>
  <span class="foot-ic" style="top:4458px"><svg width="11" height="9" viewBox="0 0 12 10"><rect x="0.5" y="0.5" width="11" height="9" rx="1" fill="none" stroke="#2b5cf3"/><path d="M1 1l5 4 5-4" fill="none" stroke="#2b5cf3"/></svg></span>
  <p class="foot-contact" style="top:4453px">Email<br>info@valtorix.design</p>

  <p class="foot-title" style="left:835px">Our Locations</p>
  <span class="foot-rule" style="left:835px"></span>
  <div class="abs" role="img" aria-label="Map showing the office location in South Wales" style="left:835px;top:4373px;width:223px;height:110px;border-radius:4px;
    background:
      radial-gradient(ellipse 60px 40px at 60px 40px,rgba(190,220,170,.9),rgba(190,220,170,0) 80%),
      radial-gradient(ellipse 90px 70px at 210px 85px,#8cc4ee,rgba(140,196,238,0) 80%),
      linear-gradient(120deg,#e2ead6 0%,#eef0ec 50%,#bcdcf3 72%,#90c6ee 100%)"></div>

  <span class="abs" style="left:0;top:4530px;width:1200px;height:1px;background:var(--line)"></span>
  <p class="copyright">© 2026 Valtorix Mechanical Design. All Rights Reserved.</p>
</footer>

</body>
</html>
```